Healthcare and Professional IT Services Company need a redesigned business card

We are a IT Services company that targets small medical practices and professional business such as Attorneys, Accounts, Architects etc. We want to communicate a professional yet friendly image using recent logo redesign here on ArtHarbor. Like to see the colors blue and orange in the design. Must use the Tall Pine Computing as displayed in the new logo - then also want to incorporate the fish logo as well.

Target Market(s)

Small medical and professional services

Industry/Entity Type

It Company

Contact Information for Business Card

The usual stuff, place for name address phone website. Also maybe our tagline which is "rooted in technology"

Requirements
Must have
• My new logo and the fish somewhere on the card

```html
<!DOCTYPE html>
<html lang="en">
<head>
<meta charset="utf-8">
<title>Tall Pine Computing — Business Card</title>
<link rel="stylesheet" href="https://fonts.googleapis.com/css2?family=Open+Sans:wght@400;600;700&display=swap">
<style>
  :root {
    --backdrop: #2a2b2d;
    --card-white: #ffffff;
    --card-silver: #eeeff0;
    --brand-blue: #1d93d8;
    --brand-blue-light: #49b4ea;
    --brand-blue-dark: #0f7fc4;
    --accent-orange: #f39a1e;
    --ink-white: #ffffff;
    --art-blue: #bfe2f6;
  }
  * { box-sizing: border-box; margin: 0; padding: 0; }
  html, body { width: 1200px; height: 871px; overflow: hidden; }
  body {
    background: var(--backdrop);
    font-family: "Open Sans", Arial, sans-serif;
    display: flex;
    align-items: center;
    justify-content: center;
    gap: 44px;
  }
  .card {
    width: 520px;
    height: 297px;
    position: relative;
    overflow: hidden;
    box-shadow: 0 10px 30px rgba(0,0,0,0.45);
  }

  /* Back of card */
  .card-back {
    background: linear-gradient(135deg, var(--card-white) 0%, var(--card-silver) 55%, #d9dadc 100%);
    display: flex;
    flex-direction: column;
    align-items: center;
    justify-content: center;
    gap: 22px;
  }
  .fish-art {
    border-radius: 50%;
    background: radial-gradient(circle, var(--art-blue) 0%, rgba(191,226,246,0.3) 100%);
  }
  .card-back .fish-art { width: 190px; height: 110px; }
  .tagline {
    color: var(--brand-blue-dark);
    font-weight: 600;
    font-size: 17px;
  }

  /* Front of card */
  .card-front {
    background: var(--card-white);
    display: flex;
  }
  .brand-side {
    width: 54%;
    display: flex;
    flex-direction: column;
    align-items: center;
    justify-content: center;
    gap: 12px;
  }
  .card-front .fish-art { width: 130px; height: 80px; }
  .brand-name {
    color: var(--brand-blue);
    font-weight: 700;
    font-size: 25px;
    letter-spacing: -0.5px;
  }
  .divider {
    width: 3px;
    background: var(--accent-orange);
  }
  .contact-side {
    flex: 1;
    background: linear-gradient(160deg, var(--brand-blue-light) 0%, var(--brand-blue) 55%, var(--brand-blue-dark) 100%);
    color: var(--ink-white);
    padding: 44px 26px 0 14px;
    text-align: right;
  }
  .person-name { font-weight: 700; font-size: 18px; }
  .person-role { font-size: 14px; margin-bottom: 16px; }
  .address { font-size: 13px; line-height: 1.35; margin-bottom: 10px; }
  .contact-line {
    display: flex;
    justify-content: flex-end;
    align-items: center;
    gap: 8px;
    font-size: 13px;
    line-height: 1.6;
  }
  .contact-line svg { width: 13px; height: 13px; flex: none; }
</style>
</head>
<body>
  <section class="card card-back">
    <div class="fish-art" role="img" aria-label="Cartoon fish mascot illustration in blue line art"></div>
    <p class="tagline">rooted in technology</p>
  </section>

  <section class="card card-front">
    <div class="brand-side">
      <div class="fish-art" role="img" aria-label="Cartoon fish mascot illustration in blue line art"></div>
      <p class="brand-name">Tall Pine Computing</p>
    </div>
    <div class="divider"></div>
    <div class="contact-side">
      <p class="person-name">Mara Quell</p>
      <p class="person-role">President</p>
      <p class="address">2107 Alder Crest Lane<br>Brookvale, NY 10990</p>
      <p class="contact-line">555 0142 7788
        <svg viewBox="0 0 16 16" aria-hidden="true"><path fill="#fff" d="M3 2h3l1 3-2 1.5a9 9 0 0 0 4.5 4.5L11 9l3 1v3a1 1 0 0 1-1 1A12 12 0 0 1 2 3a1 1 0 0 1 1-1z"/></svg>
      </p>
      <p class="contact-line">mara@tallpine.example
        <svg viewBox="0 0 16 16" aria-hidden="true"><rect x="1" y="3" width="14" height="10" rx="1" fill="#fff"/><path d="M1.5 3.5 8 9l6.5-5.5" fill="none" stroke="#1d93d8" stroke-width="1.3"/></svg>
      </p>
      <p class="contact-line">www.tallpine.example
        <svg viewBox="0 0 16 16" aria-hidden="true"><circle cx="8" cy="8" r="7" fill="#fff"/><path d="M1 8h14M8 1c-3 3.5-3 10.5 0 14M8 1c3 3.5 3 10.5 0 14" fill="none" stroke="#1d93d8" stroke-width="1"/></svg>
      </p>
    </div>
  </section>
</body>
</html>
```